Need Help having my business card stand out

I am the owner of Birchway Canine Training and would like for my business cards to stand out. I have been trying to keep designing them myself but I can't get what I have in my head on the card. I will try my best to post templates that I like for inspirations. I want something unique but elegant. I don't want in to look cartoony or cheesy. It needs to pop in a pet shop but also in a coffee shop or gym.

Target Market(s)

Dog owners, Married ,No young kids Jr High school kids and up (maybe kids on the way) Executives, Stay at home moms/wives, Small business owners

Industry/Entity Type

Dog Training

Contact Information for Business Card

Lowell Spratt, 281-904-3376, info@birchwaycanine.example, www.birchwaycanine.example

Colors

Designer to choose colors to be used in the design.

Requirements
Must have
• my logo
Should not have
• Cursive lettering

```html
<!DOCTYPE html>
<html lang="en">
<head>
<meta charset="utf-8">
<title>Birchway Canine Training — Business Card</title>
<link rel="stylesheet" href="https://fonts.googleapis.com/css2?family=Arimo:wght@400;700&family=Montserrat:wght@300;400;600&family=Open+Sans:wght@400;600&display=swap">
<style>
  :root {
    --stage: #dcdcdc;
    --card: #2c2c2b;
    --card-band: #1f1f1e;
    --gold: #e0a823;
    --gold-deep: #b8861a;
    --ink-light: #f2f2f2;
    --ink-dark: #121212;
    --icon: #2a2a2a;
    --row: 25px;
  }
  * { margin: 0; padding: 0; box-sizing: border-box; }
  html, body { width: 1200px; height: 800px; overflow: hidden; }
  body {
    background: var(--stage);
    display: flex;
    align-items: center;
    justify-content: center;
    gap: 40px;
  }
  .card {
    position: relative;
    width: 540px;
    height: 309px;
    background: var(--card);
    overflow: hidden;
    box-shadow: 0 6px 18px rgba(0,0,0,.25);
  }

  /* ---------- Front ---------- */
  .front .top-band {
    position: absolute; left: 0; right: 0; top: 0; height: 92px;
    background: var(--card-band);
  }
  .front .brand-mini {
    position: absolute; right: 26px; top: 30px;
    display: flex; align-items: center; gap: 8px;
    font-family: "Arimo", sans-serif; font-weight: 700;
    font-size: 15px; color: var(--gold);
  }
  .brand-mini .mark { width: 12px; height: 12px; border-radius: 50%; background: var(--gold); }

  .front .contact-strip {
    position: absolute; left: 236px; top: 128px;
    width: 22px; height: calc(var(--row) * 5);
    background: var(--gold);
    display: flex; flex-direction: column;
  }
  .contact-strip .cell {
    height: var(--row);
    display: flex; align-items: center; justify-content: center;
  }
  .contact-strip svg { width: 11px; height: 11px; }

  .front .contact-list {
    position: absolute; left: 270px; top: 128px;
    list-style: none;
    font-family: "Open Sans", sans-serif; font-size: 11px;
    color: var(--ink-light); line-height: var(--row);
    white-space: nowrap;
  }

  .front .holder {
    position: absolute; left: 40px; top: 232px;
    font-family: "Arimo", sans-serif;
  }
  .holder .name { font-size: 22px; color: var(--ink-light); font-weight: 400; }
  .holder .name b { font-weight: 700; }
  .holder .role { font-size: 13px; color: var(--gold); font-weight: 700; margin-top: 2px; }

  /* ---------- Back ---------- */
  .back .bottom-band {
    position: absolute; left: 0; right: 0; bottom: 0; height: 110px;
    background: var(--card-band);
  }
  .back .brand {
    position: absolute; left: 0; right: 0; top: 86px;
    display: flex; align-items: center; justify-content: center; gap: 12px;
    font-family: "Arimo", sans-serif; font-weight: 700;
    font-size: 28px; color: var(--ink-dark);
  }
  .brand .mark { width: 22px; height: 22px; border-radius: 50%; background: var(--ink-dark); }
  .back .commands {
    position: absolute; left: 40px; bottom: 44px;
    font-family: "Montserrat", sans-serif; font-weight: 400;
    font-size: 16px; letter-spacing: 2px; color: var(--gold);
    display: flex; align-items: center; gap: 12px;
  }
  .commands .dot { width: 4px; height: 4px; border-radius: 50%; background: var(--gold); }
  .back .fold {
    position: absolute; right: 38px; bottom: 42px; width: 34px; height: 22px;
  }
</style>
</head>
<body>

  <section class="card front" aria-label="Business card front">
    <div class="top-band"></div>
    <div class="brand-mini"><span class="mark"></span>Birchway Canine Training</div>

    <div class="contact-strip" aria-hidden="true">
      <span class="cell"><svg viewBox="0 0 12 12"><path d="M6 0.5a4 4 0 0 1 4 4c0 3-4 7-4 7s-4-4-4-7a4 4 0 0 1 4-4z" fill="var(--icon)"/><circle cx="6" cy="4.5" r="1.4" fill="var(--gold)"/></svg></span>
      <span class="cell"><svg viewBox="0 0 12 12"><rect x="3" y="0.5" width="6" height="11" rx="1.2" fill="var(--icon)"/><rect x="4" y="2" width="4" height="7" fill="var(--gold)"/></svg></span>
      <span class="cell"><svg viewBox="0 0 12 12"><rect x="1" y="3" width="10" height="7" rx="1" fill="var(--icon)"/><rect x="3" y="1" width="6" height="3" fill="var(--icon)"/><rect x="3" y="5" width="6" height="1.2" fill="var(--gold)"/></svg></span>
      <span class="cell"><svg viewBox="0 0 12 12"><rect x="0.5" y="2" width="11" height="8" fill="var(--icon)"/><path d="M1 2.5l5 4 5-4" stroke="var(--gold)" stroke-width="1" fill="none"/></svg></span>
      <span class="cell"><svg viewBox="0 0 12 12"><circle cx="6" cy="6" r="5.5" fill="var(--icon)"/><path d="M0.5 6h11M6 0.5v11M6 0.5c-3 3-3 8 0 11M6 0.5c3 3 3 8 0 11" stroke="var(--gold)" stroke-width=".7" fill="none"/></svg></span>
    </div>

    <ul class="contact-list">
      <li>120 Alder Ln, Suite 300, Fairbrook, US 0000</li>
      <li>281.904.3376</li>
      <li>281.904.3377</li>
      <li>info@birchwaycanine.example</li>
      <li>www.birchwaycanine.example</li>
    </ul>

    <div class="holder">
      <p class="name"><b>Lowell</b> Spratt</p>
      <p class="role">Designation</p>
    </div>
  </section>

  <section class="card back" aria-label="Business card back">
    <div class="bottom-band"></div>
    <div class="brand"><span class="mark"></span>Birchway Canine Training</div>

    <div class="commands">
      <span>COME</span><span class="dot"></span>
      <span>SIT</span><span class="dot"></span>
      <span>DOWN</span><span class="dot"></span>
      <span>STAY</span><span class="dot"></span>
      <span>GOOD</span>
    </div>

    <svg class="fold" viewBox="0 0 34 22" aria-hidden="true">
      <polygon points="0,8 17,0 34,8 17,16" fill="var(--gold)"/>
      <polygon points="17,16 34,8 34,14 17,22" fill="var(--gold-deep)"/>
    </svg>
  </section>

</body>
</html>
```